Professional & attention grabbing.

A business card design, front and back. I already have a logo I will attach, but I am open to something new as well.
Things to include:
Name:
Title:
Phone:
Email:
Wanting something that is professional but attention grabbing.
Also we do a lot of work using drones on natural gas pipelines (leading the future)if you want to include any of that. I'm open to ideas.
Target Market(s)
Natural gas transmission industry / greenhouse gas mitigation industry
Industry/Entity Type
Business
Colors
Designer to choose colors to be used in the design.
Look and feel
Each slider illustrates characteristics of the customer's brand and the style your logo design should communicate.

```html
<!DOCTYPE html>
<html lang="en">
<head>
<meta charset="utf-8">
<title>Ridgeway Inspections – Business Card</title>
<link href="https://fonts.googleapis.com/css2?family=Roboto:wght@300;400;700&display=swap" rel="stylesheet">
<style>
  :root {
    --backdrop: #3b3431;
    --card: #161616;
    --card-edge: #1f1f1f;
    --accent: #c0262d;
    --text-light: #f2f2f2;
    --text-muted: #9a9a9a;
    --brand-grey: #a7a7a7;
    --rule: #8a8a8a;
  }
  * { box-sizing: border-box; margin: 0; padding: 0; }
  html, body {
    width: 1200px; height: 864px; overflow: hidden;
    background: var(--backdrop);
    font-family: "Roboto", Arial, sans-serif;
  }
  .sheet {
    width: 1200px; height: 864px;
    display: flex; align-items: center; justify-content: center; gap: 40px;
  }
  .card {
    position: relative;
    width: 540px; height: 309px;
    background: var(--card);
    border: 1px solid var(--card-edge);
    box-shadow: 0 10px 30px rgba(0,0,0,.35);
  }
  /* Brand name */
  .brand {
    display: flex; align-items: center; gap: 12px;
  }
  .brand__mark {
    width: 22px; height: 22px; background: var(--accent);
  }
  .brand__name {
    font-weight: 700; font-size: 30px; letter-spacing: .5px;
    text-transform: uppercase; line-height: 1;
  }
  /* Front */
  .card--front .brand {
    position: absolute; left: 50%; top: 118px; transform: translateX(-50%);
    white-space: nowrap;
  }
  .card--front .brand__name { color: var(--brand-grey); }
  .card--front .website {
    position: absolute; left: 0; right: 0; top: 200px;
    text-align: center; color: var(--text-muted);
    font-size: 13px; font-weight: 300; letter-spacing: 5px;
  }
  /* Back */
  .card--back .brand {
    position: absolute; right: 32px; top: 54px;
  }
  .card--back .brand__name { color: var(--text-light); font-size: 22px; }
  .card--back .brand__mark { width: 16px; height: 16px; }
  .person { position: absolute; left: 34px; top: 126px; }
  .person__name {
    color: var(--accent); font-size: 17px; font-weight: 400;
    text-transform: uppercase; letter-spacing: .5px;
  }
  .person__title {
    color: var(--text-light); font-size: 14px; font-weight: 400;
    text-transform: uppercase; margin-top: 2px;
    padding-bottom: 8px; border-bottom: 1px solid var(--rule); width: 190px;
  }
  .contacts {
    list-style: none; margin-top: 10px;
  }
  .contacts__item {
    display: flex; align-items: center; gap: 10px;
    color: var(--text-light); font-size: 13px; font-weight: 300;
    line-height: 21px;
  }
  .contacts__icon { width: 11px; height: 11px; fill: var(--accent); flex: none; }
  .card--back .baseline {
    position: absolute; left: 210px; right: 32px; top: 270px;
    border-top: 1px solid var(--rule);
  }
</style>
</head>
<body>
<main class="sheet">
  <section class="card card--front" aria-label="Card front">
    <div class="brand">
      <span class="brand__mark"></span>
      <span class="brand__name">Ridgeway Inspections</span>
    </div>
    <p class="website">www.ridgewayinspect.com</p>
  </section>

  <section class="card card--back" aria-label="Card back">
    <div class="brand">
      <span class="brand__mark"></span>
      <span class="brand__name">Ridgeway Inspections</span>
    </div>
    <div class="person">
      <h1 class="person__name">Mark Hale</h1>
      <p class="person__title">President</p>
      <ul class="contacts">
        <li class="contacts__item">
          <svg class="contacts__icon" viewBox="0 0 12 12" aria-hidden="true"><path d="M3 0h2l1 3-1.5 1a7 7 0 0 0 3.5 3.5L9 6l3 1v2a3 3 0 0 1-3 3A9 9 0 0 1 0 3a3 3 0 0 1 3-3z"/></svg>
          555 0142 7781
        </li>
        <li class="contacts__item">
          <svg class="contacts__icon" viewBox="0 0 12 12" aria-hidden="true"><path d="M0 2h12v1L6 7 0 3z"/><path d="M0 4.3l6 4 6-4V10H0z"/></svg>
          mark@ridgewayinspect.com
        </li>
        <li class="contacts__item">
          <svg class="contacts__icon" viewBox="0 0 12 12" aria-hidden="true"><circle cx="6" cy="6" r="6"/><path d="M6 1v10M1 6h10" stroke="#161616" stroke-width="1" fill="none"/></svg>
          www.ridgewayinspect.com
        </li>
      </ul>
    </div>
    <div class="baseline"></div>
  </section>
</main>
</body>
</html>
```